Business Card Design for a Personal Trainer

I need a business card design for my job as a personal trainer. It should have a unique, modern and exclusive design. On the front there should be only my logo with my name and my job. 0162/3819204 Tobias Lendhart Wiesengrundweg 14 80417 Munich Germany The most important contact information is the web adress. it can be bigger than the rest, but its not necessary. The card should be 8,5cmx5,5cm big. Font: Roboto. Colors: black, white, gray, 56c1ff.

```html
<!DOCTYPE html>
<html lang="de">
<head>
<meta charset="utf-8">
<title>Tobias Lendhart – Personal Trainer Business Card</title>
<link rel="stylesheet" href="https://fonts.googleapis.com/css2?family=Work+Sans:wght@400;500;600&display=swap">
<style>
  :root {
    --backdrop: #3a3330;
    --card-black: #111111;
    --card-black-soft: #1d1d1d;
    --card-white: #ffffff;
    --ink: #151515;
    --ink-soft: #3c3c3c;
    --rule: #1a1a1a;
    --photo-dark: #1c1c1c;
    --photo-mid: #5a5a5a;
  }
  * { box-sizing: border-box; margin: 0; padding: 0; }
  html, body { width: 1200px; height: 715px; overflow: hidden; }
  body {
    background: var(--backdrop);
    font-family: "Work Sans", Arial, sans-serif;
    position: relative;
  }
  .card {
    position: absolute;
    top: 190px;
    width: 520px;
    height: 336px;
    overflow: hidden;
    box-shadow: 0 10px 30px rgba(0,0,0,.45);
  }

  /* Front */
  .card-front {
    left: 60px;
    background: linear-gradient(135deg, var(--card-black-soft), var(--card-black));
  }
  .portrait {
    position: absolute;
    left: 20px;
    top: 20px;
    width: 250px;
    height: 316px;
    background: radial-gradient(ellipse at 50% 30%, var(--photo-mid) 0%, var(--photo-dark) 65%, transparent 100%);
  }
  .front-identity {
    position: absolute;
    left: 270px;
    top: 160px;
    width: 230px;
    color: var(--card-white);
    text-align: center;
  }
  .identity-mark {
    display: block;
    width: 34px;
    height: 34px;
    margin: 0 auto 14px;
    background: var(--card-white);
  }
  .identity-name {
    font-size: 24px;
    font-weight: 500;
    letter-spacing: .5px;
    line-height: 1;
    white-space: nowrap;
  }
  .identity-role {
    display: flex;
    align-items: center;
    gap: 8px;
    margin-top: 6px;
    font-size: 10px;
    letter-spacing: 3px;
    white-space: nowrap;
  }
  .identity-role::before,
  .identity-role::after {
    content: "";
    flex: 1;
    height: 1px;
    background: currentColor;
  }

  /* Back */
  .card-back {
    left: 620px;
    background: var(--card-white);
    color: var(--ink);
  }
  .back-band {
    position: absolute;
    left: 0;
    bottom: 0;
    width: 520px;
    height: 120px;
  }
  .holder {
    position: absolute;
    left: 36px;
    top: 40px;
  }
  .holder-name {
    font-size: 17px;
    font-weight: 600;
    letter-spacing: .8px;
  }
  .holder-role {
    font-size: 13px;
    color: var(--ink-soft);
    margin-top: 3px;
  }
  .contact-list {
    list-style: none;
    position: absolute;
    left: 36px;
    top: 112px;
    font-size: 13px;
    line-height: 22px;
    color: var(--ink);
  }
  .contact-list li { display: flex; align-items: center; gap: 8px; }
  .contact-list svg { width: 9px; height: 9px; flex: none; }
  .divider {
    position: absolute;
    left: 150px;
    top: 190px;
    width: 340px;
    height: 1.5px;
    background: var(--rule);
  }
  .back-identity {
    position: absolute;
    right: 26px;
    top: 56px;
    width: 220px;
    color: var(--ink);
    text-align: center;
  }
  .back-identity .identity-mark { background: var(--ink); width: 30px; height: 30px; margin-bottom: 12px; }
  .back-identity .identity-name { font-size: 22px; }
  .back-identity .identity-role { font-size: 9px; }
  .address {
    position: absolute;
    right: 36px;
    top: 238px;
    font-size: 14px;
    line-height: 22px;
    text-align: right;
    color: var(--ink);
  }
</style>
</head>
<body>

<section class="card card-front" aria-label="Business card front">
  <div class="portrait" role="img" aria-label="Black and white portrait of the trainer with crossed arms"></div>
  <div class="front-identity">
    <span class="identity-mark"></span>
    <div class="identity-name">TOBIAS LENDHART</div>
    <div class="identity-role">PERSONAL TRAINER</div>
  </div>
</section>

<section class="card card-back" aria-label="Business card back">
  <svg class="back-band" viewBox="0 0 520 120" aria-hidden="true">
    <path d="M0 8 L150 90 Q160 96 180 96 L520 96 L520 120 L0 120 Z" fill="var(--card-black)"/>
    <path d="M0 0 L158 86 Q166 90 180 90 L520 90 L520 92 L180 92 Q164 92 156 88 L0 4 Z" fill="var(--photo-mid)"/>
  </svg>

  <div class="holder">
    <div class="holder-name">TOBIAS LENDHART</div>
    <div class="holder-role">Personal Trainer</div>
  </div>

  <ul class="contact-list">
    <li><svg viewBox="0 0 10 10"><path d="M2 1 L4 1 L4.5 3 L3.4 3.8 Q4.3 5.8 6.2 6.6 L7 5.5 L9 6 L9 8 Q9 9 8 9 Q1 8.5 1 2 Q1 1 2 1 Z" fill="currentColor"/></svg>0162/3819204</li>
    <li><svg viewBox="0 0 10 10"><rect x="1" y="2" width="8" height="6" fill="none" stroke="currentColor"/><path d="M1 2 L5 5.5 L9 2" fill="none" stroke="currentColor"/></svg>t.lendhart@postfach.de</li>
    <li><svg viewBox="0 0 10 10"><circle cx="5" cy="5" r="4" fill="none" stroke="currentColor"/><path d="M1 5 H9 M5 1 Q2.5 5 5 9 M5 1 Q7.5 5 5 9" fill="none" stroke="currentColor" stroke-width=".8"/></svg>www.lendhart-training.de</li>
  </ul>

  <div class="divider"></div>

  <div class="back-identity">
    <span class="identity-mark"></span>
    <div class="identity-name">TOBIAS LENDHART</div>
    <div class="identity-role">PERSONAL TRAINER</div>
  </div>

  <address class="address" style="font-style:normal">
    Wiesengrundweg 14<br>80417 München
  </address>
</section>

</body>
</html>
```